Quillmarsh Property Solutions need a business card design

Hello guys. We would need a business card design asap please.
We are a start up property investment business based in London UK specialised in buying, selling, managing and letting properties and helping distressed property owners.
The name of our Business is Quillmarsh, the logo symbolises the four fundamental elements of the world (earth, air, fire and water) and so it stands for strength, stability, longevity.
We would like the business card to communicate professionalism and reliability. Many many thanks indeed for your work.

Details:

1.) Rosalind Updike
Property Investor
Mobile: +44(0)7700123456
Email: rosalind.quillmarsh@mailbox-example.com

2.) Dominic Updike
Property Investor
Mobile: +44(0)7700987654
Email: dominic.quillmarsh@mailbox-example.com

```html
<!DOCTYPE html>
<html lang="en">
<head>
<meta charset="utf-8">
<title>Quillmarsh Property Solutions – Business Card</title>
<link rel="stylesheet" href="https://fonts.googleapis.com/css2?family=Jost:wght@500;600&family=Open+Sans:wght@400&display=swap">
<style>
  :root {
    --backdrop: #d4d4d6;
    --card: #ffffff;
    --brand-red: #d1202e;
    --brand-blue: #2f5aa8;
    --brand-green: #16893f;
    --wordmark-grey: #8c8c8e;
    --ghost-grey: #efefef;
    --ink-white: #ffffff;
  }
  * { box-sizing: border-box; margin: 0; padding: 0; }
  html, body {
    width: 883px;
    height: 1200px;
    overflow: hidden;
    background: var(--backdrop);
  }
  .stage {
    position: relative;
    width: 883px;
    height: 1200px;
  }
  .card {
    position: absolute;
    left: 91px;
    width: 700px;
    background: var(--card);
    box-shadow: 0 4px 10px rgba(0, 0, 0, 0.22);
    overflow: hidden;
  }

  /* Front */
  .card--front { top: 150px; height: 391px; }
  .front-mark {
    position: absolute;
    left: 0;
    top: 60px;
    width: 270px;
    height: 270px;
    background: var(--brand-blue);
  }
  .front-wordmark {
    position: absolute;
    right: 40px;
    top: 262px;
    text-align: right;
    font-family: "Jost", sans-serif;
    font-weight: 600;
    color: var(--wordmark-grey);
  }
  .front-wordmark .name { font-size: 58px; line-height: 1; letter-spacing: 1px; }
  .front-wordmark .tagline { font-size: 26px; line-height: 1; margin-top: 10px; letter-spacing: 1px; }

  /* Back */
  .card--back { top: 581px; height: 364px; }
  .back-ghost {
    position: absolute;
    left: 300px;
    top: 70px;
    font-family: "Jost", sans-serif;
    font-weight: 600;
    color: var(--ghost-grey);
    line-height: 1;
    transform: rotate(-13deg);
    transform-origin: left top;
  }
  .back-ghost .name { font-size: 62px; }
  .back-ghost .tagline { font-size: 32px; margin-top: 6px; padding-left: 10px; }
  .back-mark {
    position: absolute;
    left: 94px;
    top: 30px;
    width: 112px;
    height: 112px;
    background: var(--brand-blue);
  }
  .back-wordmark {
    position: absolute;
    left: 44px;
    top: 164px;
    width: 212px;
    font-family: "Jost", sans-serif;
    font-weight: 600;
    color: var(--wordmark-grey);
    text-align: center;
  }
  .back-wordmark .name { font-size: 31px; line-height: 1; letter-spacing: 0.5px; }
  .back-wordmark .tagline { font-size: 11px; line-height: 1; margin-top: 9px; letter-spacing: 0.5px; }

  .contact-bar {
    position: absolute;
    left: 32px;
    width: 632px;
    display: flex;
    align-items: center;
    padding-left: 26px;
    font-family: "Open Sans", sans-serif;
    color: var(--ink-white);
    white-space: nowrap;
  }
  .contact-bar--name { top: 232px; height: 41px; background: var(--brand-red); font-size: 22px; }
  .contact-bar--name .divider {
    display: inline-block;
    width: 1.5px;
    height: 26px;
    background: var(--ink-white);
    margin: 0 12px;
  }
  .contact-bar--name .role { font-size: 18px; }
  .contact-bar--phone { top: 276px; height: 26px; background: var(--brand-blue); font-size: 17px; }
  .contact-bar--email { top: 305px; height: 27px; background: var(--brand-green); font-size: 17px; }
  .contact-bar svg { margin-right: 14px; flex: none; }

  .footer-stripes {
    position: absolute;
    right: 0;
    bottom: 0;
    width: 306px;
    height: 19px;
    display: flex;
  }
  .footer-stripes span { flex: 1; }
  .footer-stripes .green { background: var(--brand-green); }
  .footer-stripes .blue { background: var(--brand-blue); }
  .footer-stripes .red { background: var(--brand-red); }
</style>
</head>
<body>
<main class="stage">

  <section class="card card--front" aria-label="Business card front">
    <div class="front-mark"></div>
    <div class="front-wordmark">
      <p class="name">QUILLMARSH</p>
      <p class="tagline">PROPERTY SOLUTIONS</p>
    </div>
  </section>

  <section class="card card--back" aria-label="Business card back">
    <div class="back-ghost" aria-hidden="true">
      <p class="name">QUILLMARSH</p>
      <p class="tagline">PROPERTY SOLUTIONS</p>
    </div>

    <div class="back-mark"></div>
    <div class="back-wordmark">
      <p class="name">QUILLMARSH</p>
      <p class="tagline">PROPERTY SOLUTIONS</p>
    </div>

    <div class="contact-bar contact-bar--name">
      <span class="person">Rosalind Updike</span>
      <span class="divider"></span>
      <span class="role">Property Investor</span>
    </div>

    <div class="contact-bar contact-bar--phone">
      <svg width="11" height="17" viewBox="0 0 11 17" aria-hidden="true">
        <rect x="1" y="1" width="9" height="15" rx="1.5" fill="none" stroke="#fff" stroke-width="1.4"/>
        <line x1="4" y1="13.5" x2="7" y2="13.5" stroke="#fff" stroke-width="1.2"/>
      </svg>
      <span>+44(0)7700123456</span>
    </div>

    <div class="contact-bar contact-bar--email">
      <svg width="15" height="11" viewBox="0 0 15 11" aria-hidden="true">
        <rect x="0" y="0" width="15" height="11" fill="#fff"/>
        <polyline points="0.5,0.5 7.5,6 14.5,0.5" fill="none" stroke="#16893f" stroke-width="1.3"/>
      </svg>
      <span>rosalind.quillmarsh@mailbox-example.com</span>
    </div>

    <div class="footer-stripes">
      <span class="green"></span>
      <span class="blue"></span>
      <span class="red"></span>
    </div>
  </section>

</main>
</body>
</html>
```